Business Card Re-Design/Update

We'd like to update out business cards. I've included our current "Style guide" which has the colour scheme of the organisation in it. I've also included the branding files with logos etc in them.

I've also included a copy of one of our existing cards so that you can see how ugly/dated they look. I'd like a fresh modern corporate look.

Target Market(s)

These are for our clients, potential clients, industry contacts - like all business cards

Contact Information for Business Card

Name
Position
Company Address - Level 1, 47 Fernby Street, Carlow Qld 4072
Direct Phone
mobile
Email
Website -www.korvalit.com.au
Logo

Colors

Designer to choose colors to be used in the design.

Requirements
Must have
• Main Logo
• Cards will need to be editable to be able to personalize them for each new employee.
Nice to have
• The MapOut, ShipWell, KeepSteady would be okay to have if they can be sensibly and professionally added to the look without detracting from the main imagery.
• Maybe they could go on the back of the card? will leave this to your creative discretion as to whether/where they fit.
Should not have
• Should not have decorative or script fonts

```html
<!DOCTYPE html>
<html lang="en">
<head>
<meta charset="utf-8">
<title>korvalIT business card</title>
<link href="https://fonts.googleapis.com/css2?family=Lato:wght@400;700;900&display=swap" rel="stylesheet">
<style>
  :root {
    --brand-red: #c8161d;
    --brand-red-light: #e0363a;
    --brand-red-deep: #b01219;
    --ink: #333335;
    --ink-soft: #555558;
    --paper: #f7f7f7;
    --stage: #2b2b2d;
    --rule: #9a9a9a;
  }
  * { box-sizing: border-box; margin: 0; padding: 0; }
  html, body {
    width: 1200px; height: 997px; overflow: hidden;
    background: var(--stage);
    font-family: "Lato", Arial, sans-serif;
  }
  .sheet {
    position: relative; width: 1200px; height: 997px;
    display: flex; flex-direction: column; align-items: center; justify-content: center; gap: 48px;
  }
  .card {
    position: relative; width: 640px; height: 366px; overflow: hidden;
    border-radius: 3px; box-shadow: 0 12px 30px rgba(0,0,0,.45);
  }

  /* Back of card */
  .card--back { background: var(--brand-red); }
  .card__texture {
    position: absolute; inset: 0;
    background: linear-gradient(135deg, var(--brand-red-light) 0%, var(--brand-red) 55%, var(--brand-red-deep) 100%);
  }
  .card--back .brand {
    position: absolute; left: 0; right: 0; top: 120px;
    display: flex; justify-content: center; align-items: center; gap: 18px;
  }
  .brand__mark { width: 54px; height: 54px; background: #fff; flex-shrink: 0; }
  .brand__name { font-weight: 900; font-size: 74px; letter-spacing: -1px; line-height: 1; color: #fff; white-space: nowrap; }
  .card--back .web {
    position: absolute; left: 0; right: 0; top: 232px; text-align: center;
    color: #fff; font-weight: 700; font-size: 15px; letter-spacing: 7px; text-transform: uppercase;
  }

  /* Front of card */
  .card--front { background: var(--paper); }
  .card--front .brand {
    position: absolute; left: 150px; top: 62px; display: flex; align-items: center; gap: 12px;
  }
  .card--front .brand__mark { width: 40px; height: 40px; background: var(--brand-red); }
  .card--front .brand__name { font-size: 52px; color: var(--ink); }

  .person { position: absolute; right: 345px; top: 150px; text-align: right; }
  .person__name { color: var(--brand-red); font-weight: 900; font-size: 17px; text-transform: uppercase; line-height: 1.2; }
  .person__role { color: var(--ink-soft); font-size: 13px; margin-top: 2px; }
  .person__address { color: var(--brand-red); font-weight: 900; font-size: 15px; line-height: 1.3; margin-top: 18px; }

  .divider {
    position: absolute; left: 318px; top: 144px; width: 2px; height: 114px;
    background: linear-gradient(to bottom, transparent, var(--rule) 40%, var(--rule) 60%, transparent);
  }

  .contacts { position: absolute; left: 340px; top: 152px; list-style: none; }
  .contacts li {
    display: flex; align-items: center; gap: 10px; height: 24px;
    font-size: 14px; color: var(--ink); white-space: nowrap;
  }
  .contacts .note { font-size: 11px; color: var(--ink-soft); margin-left: 2px; }
  .icon {
    width: 18px; height: 18px; border-radius: 50%; background: var(--brand-red);
    display: inline-flex; align-items: center; justify-content: center; flex-shrink: 0;
  }
  .icon svg { width: 10px; height: 10px; fill: #fff; }

  .swoosh { position: absolute; left: 0; bottom: 0; width: 640px; height: 140px; }
</style>
</head>
<body>
<main class="sheet">

  <section class="card card--back" aria-label="Card back">
    <div class="card__texture" role="img" aria-label="Red faceted low-poly background pattern"></div>
    <div class="brand">
      <span class="brand__mark"></span>
      <span class="brand__name">korvalIT</span>
    </div>
    <p class="web">www.korvalit.com.au</p>
  </section>

  <section class="card card--front" aria-label="Card front">
    <div class="brand">
      <span class="brand__mark"></span>
      <span class="brand__name">korvalIT</span>
    </div>

    <div class="person">
      <p class="person__name">Dana Whitfield</p>
      <p class="person__role">Business Development Manager</p>
      <p class="person__address">Level 1, 47 Fernby Street<br>Carlow Qld 4072</p>
    </div>

    <div class="divider"></div>

    <ul class="contacts">
      <li>
        <span class="icon"><svg viewBox="0 0 10 10"><path d="M1 4.5C1 2.5 3 1.8 5 1.8s4 .7 4 2.7H7.2V3.8H2.8v.7zM2.5 5h5l1 4h-7z"/></svg></span>
        +61 (0)400 555 018
      </li>
      <li>
        <span class="icon"><svg viewBox="0 0 10 10"><path d="M1 4h8v4H7.5V6.5h-5V8H1zM2.5 1h5v2.5h-5zM3 7h4v2H3z"/></svg></span>
        +61 (0)7 5550 1240
      </li>
      <li>
        <span class="icon"><svg viewBox="0 0 10 10"><path d="M2 1l2 2-1 1.5c.7 1.3 1.2 1.8 2.5 2.5L7 6l2 2-1.5 1.5C4 9 1 6 .5 2.5z"/></svg></span>
        +61 (0)7 5550 1247 <span class="note">(Direct)</span>
      </li>
      <li>
        <span class="icon"><svg viewBox="0 0 10 10"><path d="M1 2.5h8v5H1z"/><path d="M1.3 2.8l3.7 2.8 3.7-2.8" fill="none" stroke="#c8161d" stroke-width=".8"/></svg></span>
        dwhitfield@korvalit.com.au
      </li>
    </ul>

    <svg class="swoosh" viewBox="0 0 640 140" preserveAspectRatio="none" aria-hidden="true">
      <path d="M0 140 L0 118 C220 120 470 80 640 10 L640 140 Z" fill="#c8161d"/>
      <path d="M210 116 C400 104 540 60 640 0 L640 14 C520 72 380 108 210 116 Z" fill="#333335"/>
    </svg>
  </section>

</main>
</body>
</html>
```